Business card for Luxury Portable Restroom Trailer company

We are a Luxury Portable Restroom Trailer Company Called FALCRIDGE HIRES. Based in Orange County California. We provide portable restroom trailers for events, such as, Weddings, Concerts, Charity events, Sporting events, Tournaments, Corporate events, ect. We rent and Sell the Luxury restrooms. Our colors are white, grey, and Orange. As you will see in the logo we uploaded.
There are 2 people in the company so the names and titles will change for the 3 people but card will remain the same. Here is the information for each Person: Dwight Penner CFO 555 318-0476
next Person: Leon Marchetti VP 555 318-0476
Next Person: Owen Marchetti CEO 555 318-0476
Information to include on the card: Luxury Restroom Trailers Rental and Sales. Weddings, Concerts, Charity, Sporting and Corp. Events.

```html
<!DOCTYPE html>
<html lang="en">
<head>
<meta charset="utf-8">
<title>Falcridge Hires – Business Card</title>
<link href="https://fonts.googleapis.com/css2?family=Open+Sans:wght@400;600&family=Bowlby+One&display=swap" rel="stylesheet">
<style>
  :root {
    --bg: #232323;
    --card: #1f1f21;
    --card-warm: #2a2523;
    --orange: #f26b21;
    --white: #f4f4f4;
    --grey: #8a8a8a;
  }
  * { margin: 0; padding: 0; box-sizing: border-box; }
  html, body { width: 1200px; height: 768px; overflow: hidden; background: var(--bg); }
  .canvas {
    position: relative; width: 1200px; height: 768px;
    display: flex; align-items: center; justify-content: center; gap: 48px;
  }
  .card {
    position: relative; width: 525px; height: 300px;
    border-radius: 18px; overflow: hidden;
    background: var(--card);
    border-bottom: 4px solid var(--orange);
    box-shadow: 0 0 0 2px var(--orange), 0 18px 40px rgba(0,0,0,.55);
    font-family: "Open Sans", sans-serif; color: var(--white);
  }
  /* Back side */
  .card-back .pattern {
    position: absolute; inset: 0;
    background: linear-gradient(200deg, #6a6a6a 0%, #2b2b2d 30%, #151516 70%, #1c1c1d 100%);
  }
  .brand {
    display: flex; align-items: center; gap: 8px;
    font-family: "Open Sans", sans-serif; font-weight: 600;
    color: var(--orange); letter-spacing: .06em; white-space: nowrap;
  }
  .brand-mark { width: 12px; height: 12px; background: var(--orange); }
  .card-back .brand { position: absolute; right: 34px; bottom: 52px; font-size: 20px; }
  /* Front side */
  .card-front .silhouette {
    position: absolute; right: 40px; top: 30px; width: 320px; height: 240px;
    border-radius: 50% 40% 45% 55%;
    background: radial-gradient(ellipse at 60% 40%, var(--card-warm) 0%, rgba(42,37,35,0) 70%);
  }
  .card-front .brand { position: absolute; left: 30px; top: 34px; font-size: 24px; }
  .person { position: absolute; right: 26px; top: 36px; display: flex; gap: 8px; text-align: right; }
  .person-name { font-weight: 600; font-size: 24px; color: var(--orange); line-height: 1.1; }
  .person-title { font-size: 12px; color: var(--white); }
  .person-bar { width: 10px; height: 44px; background: var(--orange); }
  .contacts { position: absolute; left: 30px; top: 140px; list-style: none; font-size: 14px; line-height: 1.55; }
  .contacts li { display: flex; align-items: center; gap: 8px; }
  .contacts svg { width: 12px; height: 12px; fill: var(--orange); flex: none; }
  .services { position: absolute; left: 30px; right: 26px; bottom: 20px; list-style: none; font-size: 13px; }
  .services li { display: inline-flex; align-items: center; gap: 5px; margin-right: 8px; line-height: 1.7; }
  .services li::before { content: ""; width: 7px; height: 7px; background: var(--orange); }
</style>
</head>
<body>
<main class="canvas">
  <section class="card card-back">
    <div class="pattern" role="img" aria-label="Repeating brand pattern with a glossy light sweep"></div>
    <div class="brand"><span class="brand-mark"></span>FALCRIDGE HIRES</div>
  </section>

  <section class="card card-front">
    <div class="silhouette" role="img" aria-label="Large faint brand silhouette in the background"></div>
    <div class="brand"><span class="brand-mark"></span>FALCRIDGE HIRES</div>
    <div class="person">
      <div>
        <div class="person-name">Dwight Penner</div>
        <div class="person-title">CFO</div>
      </div>
      <div class="person-bar"></div>
    </div>
    <ul class="contacts">
      <li><svg viewBox="0 0 24 24"><path d="M6.6 10.8a15 15 0 0 0 6.6 6.6l2.2-2.2a1 1 0 0 1 1-.25 11.4 11.4 0 0 0 3.6.57 1 1 0 0 1 1 1V20a1 1 0 0 1-1 1A17 17 0 0 1 3 4a1 1 0 0 1 1-1h3.5a1 1 0 0 1 1 1c0 1.25.2 2.45.57 3.6a1 1 0 0 1-.25 1z"/></svg>555 318-0476</li>
      <li><svg viewBox="0 0 24 24"><path d="M2 5h20v14H2zm2 2v.5l8 5 8-5V7l-8 5z"/></svg>info@falcridgehires.com</li>
      <li><svg viewBox="0 0 24 24"><path d="M12 2a10 10 0 1 0 0 20 10 10 0 0 0 0-20zm0 2c.9 1.2 1.6 2.9 1.9 5h-3.8c.3-2.1 1-3.8 1.9-5zM4.3 11h3.8c0 .7 0 1.3.1 2H4.3a8 8 0 0 1 0-2zm5.8 0h3.8a14 14 0 0 1 0 2h-3.8a14 14 0 0 1 0-2zm5.8 0h3.8a8 8 0 0 1 0 2h-3.8c.1-.7.1-1.3 0-2zM10.1 15h3.8c-.3 2.1-1 3.8-1.9 5-.9-1.2-1.6-2.9-1.9-5z"/></svg>www.falcridgehires.com</li>
    </ul>
    <ul class="services">
      <li>Luxury Restroom Trailers Rental and Sales</li>
      <li>Weddings</li>
      <li>Concerts</li>
      <li>Charity</li>
      <li>Sporting and Corp</li>
      <li>Events</li>
    </ul>
  </section>
</main>
</body>
</html>
```